Design eines Hausetiketts für traditionelles Weingut
Zielgruppe
Wir das Familienweingut Brandauer in Gimbsheim/Rheinhessen sind ein traditionelles Weingut das seine Reben selbst kultiviert und die Weine auch selbst ausbaut. Wir haben jeden Schritt in der Weinherstellung selbst in der Hand und vermarkten den Wein dann an unsere Privatkunden. Unsere Kundenstruktur sieht folgendermaßen aus: Wir haben 100% Privatkunden die unseren Wein konsumieren. Da jetzt die nächste Generation in den Weinbaubetrieb einsteigt und auch Ideen hat möchten wir ein Hausetikett einführen. Im Moment haben wir noch sehr viele unterschiedliche Etiketten und kein Hausetikett. Da die Verlagsetiketten immer seltener zu unseren Vorstellungen passen, möchten wir hier auf diesem Wege ein Hausetikett anfertigen lassen. Generell möchten wir unseren Außenauftritt komplett modernisieren. Sie können sich über die Vielfalt in unserem Betrieb unter www.weingut-brandauer-beispiel.de einen Überblick verschaffen. Langfristig gesehen wollen wir aber unsere Weinkarte verkleinern.
Aufgabenstellung
Wir haben uns vor ca. 1,5 Jahren hier auf dieser Website bereits ein Logo designen lassen. Es wäre schön wenn man das Logo bei den Entwürfen für die Etiketten berücksichtigen würde. Das wäre aber KEIN MUSS. Auch wäre es gut wenn man das ,,Wein' bei unserem Namen weglassen könnte.
Das Etikett sollte aus Vorder-und Rückenetikett bestehen und edel wirken. Vorne sollte die Rebsorte und die Geschmacksangabe stehen. Der Rest sollte auf das Rückenetikett.
Das Vorderetikett sollte ein richtiger Eyecatcher sein und im Supermarkt z.B. aus vielen anderen herausstechen. Das wäre ganz wichtig.
Man kann bei den Farben unterscheiden in 3 Konzepte.
Literwein als einsteiger Wein
Dann die Gutsweine und zum Schluss die Lagenweine. Alles Farblich oder im design etwas abgesetzt.

```html
<!DOCTYPE html>
<html lang="de">
<head>
<meta charset="utf-8">
<title>Brandauer Weißburgunder trocken – Vorderetikett</title>
<link rel="stylesheet" href="https://fonts.googleapis.com/css2?family=Cormorant+Garamond:wght@500;600&family=Source+Sans+3:wght@500&display=swap">
<style>
  :root {
    --page: #ffffff;
    --label-green: #1f6a5c;
    --label-green-dark: #185a4e;
    --cream: #f1ece0;
    --gold: #cdb677;
    --badge-text: #1f6a5c;
  }
  * { margin: 0; padding: 0; box-sizing: border-box; }
  html, body {
    width: 1200px; height: 1200px; overflow: hidden;
    background: var(--page);
  }
  .front-label {
    position: absolute;
    left: 170px; top: 150px;
    width: 860px; height: 900px;
    background: var(--label-green);
    box-shadow: inset 0 0 120px rgba(0,0,0,0.12);
  }
  .frame {
    position: absolute;
    left: 67px; top: 141px;
    width: 726px; height: 613px;
    border: 3px dashed var(--gold);
    border-bottom: none;
    opacity: 0.85;
  }
  .frame-base {
    position: absolute;
    top: 752px; height: 3px;
    border-top: 3px dashed var(--gold);
    opacity: 0.85;
  }
  .frame-base.left { left: 67px; width: 110px; }
  .frame-base.right { right: 67px; width: 110px; }
  .variety {
    position: absolute;
    left: 0; right: 0; top: 222px;
    text-align: center;
    font-family: "Cormorant Garamond", serif;
    font-weight: 600;
    font-size: 72px;
    color: var(--cream);
    letter-spacing: 0.5px;
  }
  .taste {
    position: absolute;
    left: 0; right: 0; top: 348px;
    text-align: center;
    font-family: "Cormorant Garamond", serif;
    font-weight: 600;
    font-size: 54px;
    color: var(--cream);
  }
  .vintage {
    position: absolute;
    left: 614px; top: 474px;
    width: 110px; height: 110px;
    border-radius: 50%;
    background: var(--cream);
    display: flex; align-items: center; justify-content: center;
    font-family: "Source Sans 3", sans-serif;
    font-weight: 500;
    font-size: 32px;
    color: var(--badge-text);
    letter-spacing: 1px;
  }
  .estate-name {
    position: absolute;
    left: 0; right: 0; top: 706px;
    text-align: center;
    font-family: "Cormorant Garamond", serif;
    font-weight: 500;
    font-size: 96px;
    line-height: 96px;
    color: var(--gold);
    letter-spacing: 1px;
    text-transform: uppercase;
  }
</style>
</head>
<body>
  <div class="front-label">
    <div class="frame"></div>
    <div class="frame-base left"></div>
    <div class="frame-base right"></div>
    <div class="variety">Weißburgunder</div>
    <div class="taste">trocken</div>
    <div class="vintage">2020</div>
    <div class="estate-name">Brandauer</div>
  </div>
</body>
</html>
```